Brivo Hair

Hello - our company Vantor 4 develops novel products for the skin, & hair care industry as well as dietary supplements. We're looking for a label design for a new product. The product is a premium hair loss/growth supplement. Our primary demo is women ages 45-65. I attached the brand logo & some competitive product designs that we find attractive.

I've been traveling & have not had the time to adequately review the designs, please be patient with me.

```html
<!DOCTYPE html>
<html lang="en">
<head>
<meta charset="utf-8">
<title>Brivo Hair – Women Supplement Label</title>
<link href="https://fonts.googleapis.com/css2?family=Montserrat:wght@400;600;700;800&family=Playfair+Display:wght@700;900&display=swap" rel="stylesheet">
<style>
  :root{
    --stage:#e9ebee;
    --navy:#0d3f8f;
    --blue:#1f6fd1;
    --sky:#5fb3ea;
    --ice:#eaf5fc;
    --ice-deep:#cfe6f6;
    --steel:#9aa4ae;
    --white:#ffffff;
    --ink:#2b3a4d;
  }
  *{box-sizing:border-box;margin:0;padding:0}
  html,body{width:692px;height:1200px;overflow:hidden;background:var(--stage)}
  .label{
    position:absolute;left:66px;top:150px;width:560px;height:900px;
    overflow:hidden;box-shadow:0 6px 24px rgba(0,0,0,.18);
    font-family:"Montserrat",Arial,sans-serif;color:var(--navy);
  }
  .label-texture{position:absolute;inset:0;
    background:radial-gradient(ellipse at 50% 40%,var(--white) 0%,var(--ice) 45%,var(--ice-deep) 100%)}
  .brand-band{position:absolute;left:0;top:0;width:100%;height:110px;
    background:linear-gradient(180deg,var(--blue),var(--navy));
    display:flex;align-items:center;justify-content:center;
    color:var(--white);font-weight:800;font-size:52px;letter-spacing:2px}
  .claim-box{position:absolute;left:40px;right:40px;top:148px;height:126px;
    border:4px solid var(--blue);background:var(--white);text-align:center}
  .claim-title{font-weight:800;font-size:40px;line-height:72px;color:var(--navy)}
  .claim-extract{background:var(--navy);color:var(--white);font-weight:700;
    font-size:25px;line-height:46px;letter-spacing:1px}
  .product-name{position:absolute;left:0;right:0;top:292px;height:120px;text-align:center;
    white-space:nowrap;font-weight:600;font-size:68px;color:var(--sky);letter-spacing:3px;line-height:120px}
  .strength-band{position:absolute;left:0;right:0;top:418px;height:58px;
    background:linear-gradient(90deg,#c4cad0,var(--steel) 50%,#c4cad0);
    color:var(--white);font-weight:800;font-size:34px;letter-spacing:2px;
    display:flex;align-items:center;justify-content:center}
  .formula{position:absolute;left:0;right:0;top:488px;text-align:center;
    font-family:"Playfair Display",Georgia,serif;font-weight:700;font-size:40px;color:var(--navy)}
  .audience{position:absolute;left:0;right:0;top:544px;height:76px;
    background:linear-gradient(90deg,var(--navy),var(--blue) 50%,var(--navy));
    color:var(--white);text-align:center;
    font-family:"Playfair Display",Georgia,serif;font-weight:900;font-size:62px;line-height:76px;letter-spacing:3px}
  .benefits{position:absolute;left:70px;right:50px;top:650px;list-style:none}
  .benefit{display:flex;align-items:center;gap:18px;margin-bottom:22px;
    font-size:17px;line-height:24px;color:var(--ink)}
  .benefit svg{flex:none}
  .count-badge{position:absolute;left:34px;top:766px;width:104px;height:104px;border-radius:50%;
    background:var(--white);border:5px solid var(--navy);z-index:2;
    display:flex;flex-direction:column;align-items:center;justify-content:center;color:var(--navy)}
  .count-number{font-weight:800;font-size:40px;line-height:40px}
  .count-unit{font-weight:700;font-size:12px;letter-spacing:1px}
  .footer-band{position:absolute;left:0;right:0;bottom:0;height:62px;
    background:linear-gradient(180deg,var(--blue),var(--navy));
    color:var(--white);font-weight:700;font-size:14px;letter-spacing:.5px;white-space:nowrap;
    display:flex;align-items:center;justify-content:center;padding-left:150px;padding-right:16px}
</style>
</head>
<body>
  <main class="label">
    <div class="label-texture" role="img" aria-label="Soft light blue hexagon texture background"></div>
    <header class="brand-band">VANTOR 4</header>
    <section class="claim-box">
      <p class="claim-title">MEDICALLY PROVEN</p>
      <p class="claim-extract">HE SHOULD 12:1 EXTRACT</p>
    </section>
    <h1 class="product-name">BRIVO HAIR</h1>
    <div class="strength-band">CLINICAL STRENGTH</div>
    <p class="formula">ADVANCE FORMULA</p>
    <p class="audience">WOMEN</p>
    <ul class="benefits">
      <li class="benefit">
        <svg width="34" height="34" viewBox="0 0 34 34"><circle cx="17" cy="17" r="15" fill="none" stroke="#1f6fd1" stroke-width="3"/><path d="M10 17l5 5 9-10" fill="none" stroke="#1f6fd1" stroke-width="3"/></svg>
        <span>Supports fuller, thicker looking hair with daily botanical nutrients.</span>
      </li>
      <li class="benefit">
        <svg width="34" height="34" viewBox="0 0 34 34"><circle cx="17" cy="17" r="15" fill="none" stroke="#1f6fd1" stroke-width="3"/><path d="M10 17l5 5 9-10" fill="none" stroke="#1f6fd1" stroke-width="3"/></svg>
        <span>Take two capsules daily with food for best visible results.</span>
      </li>
    </ul>
    <div class="count-badge"><span class="count-number">60</span><span class="count-unit">CAPSULES</span></div>
    <footer class="footer-band">PREMIUM HAIR LOSS/GROWTH SUPPLEMENT</footer>
  </main>
</body>
</html>
```